Silver Bloom Marisol's Cleaning Service Business Cards Project

A business card with all contact details with logo design on there (already have a logo) eye catching Logo and contact info on one side, full logo on the back, must target upper class residential and corporate companies, fitness companies, still keep it on the feminine side of things , must look elegant

Target Market(s)

Upper class homes and corporate companies

Industry/Entity Type

Cleaning Service

Contact Information for Business Card

Name: Marisol Quenby
Position: Director
ABN: 31647209853
Email: marisolssilvercleaning@tidymail.example
Number: 0417906354

Font styles to use
Decorative

Colors

Designer to choose colors to be used in the design.

Requirements
Must have
• Available Sydney Wide, contact info and logo on one side, full logo on the back
Nice to have
• Professional appearance
Should not have
• Cheap advert looking stuff

```html
<!DOCTYPE html>
<html lang="en">
<head>
<meta charset="utf-8">
<title>Silver Bloom – Business Card</title>
<link rel="stylesheet" href="https://fonts.googleapis.com/css2?family=Alegreya:wght@400&family=Lato:wght@400&display=swap">
<style>
  :root {
    --backdrop: #e8e9ec;
    --panel-dark: #2c3140;
    --card-white: #ffffff;
    --accent-teal: #2fe0d2;
    --text-light: #f4f5f7;
    --shadow: rgba(20, 24, 36, 0.18);
  }
  * { margin: 0; padding: 0; box-sizing: border-box; }
  html, body {
    width: 1200px;
    height: 900px;
    overflow: hidden;
    background: var(--backdrop);
  }
  .business-card {
    position: absolute;
    left: 100px;
    top: 140px;
    width: 1000px;
    height: 620px;
    display: flex;
    background: var(--card-white);
    box-shadow: 0 14px 40px var(--shadow);
  }
  .contact-side {
    position: relative;
    width: 528px;
    height: 100%;
    background: var(--panel-dark);
    border-right: 5px solid var(--accent-teal);
    text-align: right;
    padding-right: 24px;
    color: var(--text-light);
    font-family: "Lato", sans-serif;
  }
  .person-name {
    position: absolute;
    right: 24px;
    top: 152px;
    font-family: "Alegreya", serif;
    font-weight: 400;
    font-size: 38px;
    letter-spacing: 1.5px;
    color: var(--accent-teal);
    white-space: nowrap;
  }
  .person-role {
    position: absolute;
    right: 28px;
    top: 200px;
    font-size: 27px;
  }
  .business-number {
    position: absolute;
    right: 24px;
    top: 298px;
    font-size: 27px;
  }
  .contact-lines {
    position: absolute;
    right: 24px;
    top: 364px;
    font-size: 27px;
    line-height: 38px;
    white-space: nowrap;
  }
  .brand-side {
    flex: 1;
    display: flex;
    align-items: center;
    justify-content: center;
  }
  .brand-name {
    font-family: "Alegreya", serif;
    font-weight: 400;
    font-size: 40px;
    letter-spacing: 2px;
    color: var(--accent-teal);
    text-transform: uppercase;
    white-space: nowrap;
  }
</style>
</head>
<body>
  <article class="business-card">
    <section class="contact-side">
      <h1 class="person-name">MARISOL QUENBY</h1>
      <p class="person-role">Director</p>
      <p class="business-number">ABN: 31647209853</p>
      <p class="contact-lines">0417906354<br>marisolssilvercleaning@tidymail.example</p>
    </section>
    <section class="brand-side">
      <p class="brand-name">Silver Bloom</p>
    </section>
  </article>
</body>
</html>
```